Existing Website Requiring new Pages

I have an existing word press website that was built using elementor.
Website: www.tallowcrestcare.com.au
I require the Vacancies page (https://www.tallowcrestcare.com.au/vacancies/) to be modified to display our new properties along with minor tweaks to how the information is presented.
The vacancies to be displayed are the exactly the same as those that are located on the homepage of QMR website (https://qmr.org.au/)
The new pages that link off the Vacancies tab will require custom design.
There are roughly 8 pages/properties to be incorporated. i wish for the design to be very similar to that displayed in the following link; https://www.polunda.com.au/vacancies/merrylands
Along with this the back end has not been updated for the last 3 years so it also requires some maintenance.
Website is in the disability industry and the custom pages will display information relative to Property Vacancies.
I have attached a ZIP file with some design guides, the information for each of the properties (which will need to be modified to show our business name Tallowcrest Care) and the example of how it is to look based off the Polunda website.
If you guys have any suggestions or ideas on how to make this more presentable or possible i'm open to your ideas.
Target Market(s)
People looking for SDA properties custom built for people with a disability
Industry/Entity Type
Disability
Coding
Coded - Design and coding required
Number of Pages Required
5+ page

```html
<!DOCTYPE html>
<html lang="en">
<head>
<meta charset="utf-8">
<title>Vacancies | Tallowcrest Care</title>
<link rel="stylesheet" href="https://fonts.googleapis.com/css2?family=Montserrat:wght@400;500;600;700;900&display=swap">
<style>
:root{
  --pink:#f64aa0;
  --pink-soft:#f78bc6;
  --teal:#3fd0c2;
  --accent:#f08a5d;
  --ink:#1d1d1f;
  --nav:#3a3a3a;
  --muted:#8a8a8a;
  --line:#e4e4e4;
  --footer-bg:#f6f6f6;
  --bar:#232323;
  --blue:#2a8ce0;
  --navy:#2c3e8f;
}
*{box-sizing:border-box;margin:0;padding:0}
html,body{width:763px;height:1200px;overflow:hidden;background:#fff}
body{position:relative;font-family:"Montserrat",sans-serif;color:var(--ink)}
.abs{position:absolute}

/* header */
.topbar{position:absolute;left:0;top:0;width:763px;height:60px;background:#fff;z-index:3}
.topbar-curve{position:absolute;left:66px;top:40px;width:660px;height:35px;background:#fff;border-radius:0 0 34px 34px;z-index:3}
.brand{position:absolute;left:92px;top:26px;z-index:4;display:flex;align-items:center;gap:5px;font-size:10px;font-weight:700;color:var(--pink);letter-spacing:.3px}
.brand-dot{width:10px;height:10px;border-radius:50%;background:var(--pink)}
.nav{position:absolute;top:33px;left:0;z-index:4;font-size:6.6px;font-weight:700;letter-spacing:.4px;color:var(--nav)}
.nav a{position:absolute;white-space:nowrap;color:inherit;text-decoration:none}
.nav a.active{color:var(--accent)}

/* hero */
.hero{position:absolute;left:0;top:60px;width:763px;height:209px;background:var(--pink);overflow:hidden}
.hero-photo{position:absolute;left:0;top:0;width:340px;height:209px;background:linear-gradient(90deg,#8a8f95 0%,#a9a2a6 45%,rgba(246,74,160,0) 100%)}
.hero-tint{position:absolute;left:280px;top:0;width:483px;height:209px;background:radial-gradient(ellipse at 55% 45%,rgba(230,80,200,.55),rgba(246,74,160,0) 65%)}
.hero-title{position:absolute;left:327px;top:89px;font-size:51px;font-weight:900;color:#fff;letter-spacing:-.5px;line-height:1}

/* cards */
.card{position:absolute;width:286px;height:153px;border:1px solid #cfcfcf;border-radius:12px;background:#fff;overflow:hidden}
.card.featured{border-color:#bdeee8;box-shadow:0 2px 8px rgba(0,0,0,.08)}
.card-photo{position:absolute;left:10px;top:10px;width:132px;height:132px;border-radius:50%}
.card-grass{position:absolute;left:0;bottom:0;width:100%;height:10px;background:linear-gradient(90deg,rgba(63,208,194,.18),rgba(246,180,120,.18))}
.card.featured .card-grass{height:9px;background:linear-gradient(90deg,#3fd0c2 0%,#3fd0c2 40%,#f7b35b 70%,#f08a5d 100%)}
.card-head{position:absolute;top:0;height:67px;display:flex;flex-direction:column;justify-content:flex-end}
.card-title{font-size:17px;font-weight:600;line-height:19px;letter-spacing:.2px}
.card-info{position:absolute;top:72px;font-size:14px;font-weight:400;line-height:19px}
.card-info .bed{display:flex;align-items:center;gap:5px}
.card.l .card-head,.card.l .card-info{left:164px}
.card.r .card-head,.card.r .card-info{left:154px}

/* footer */
.footer{position:absolute;left:0;top:984px;width:763px;height:175px;background:var(--footer-bg)}
.foot-brand{position:absolute;left:81px;top:40px;display:flex;align-items:center;gap:5px;font-size:11px;font-weight:700;color:var(--pink)}
.contact{position:absolute;left:78px;font-size:7.5px;color:var(--muted);display:flex;align-items:center;gap:5px}
.contact svg{width:8px;height:8px}
.social{position:absolute;left:328px;width:20px;height:20px;border-radius:50%;background:var(--navy)}
.social.badge{background:#6a2c8a}
.foot-col{position:absolute;top:27px;width:139px}
.foot-col h3{font-size:8.4px;font-weight:500;letter-spacing:.3px;color:var(--ink);border-left:2px solid var(--blue);padding-left:7px;line-height:9px;height:9px;margin-bottom:11px}
.foot-col ul{list-style:none;border-top:1px solid var(--line)}
.foot-col li{font-size:7.5px;color:var(--muted);line-height:13px;padding:3px 0;border-bottom:1px solid var(--line)}
.bottom-bar{position:absolute;left:0;top:1159px;width:763px;height:41px;background:var(--bar);color:#fff;font-size:6.5px;text-align:center;line-height:41px}
.to-top{position:absolute;right:5px;top:11px;width:19px;height:19px;background:#111;display:flex;align-items:center;justify-content:center}
</style>
</head>
<body>

<header>
  <div class="topbar"></div>
  <div class="topbar-curve"></div>
  <div class="brand"><span class="brand-dot"></span>Tallowcrest Care</div>
  <nav class="nav">
    <a style="left:333px">HOME</a>
    <a style="left:372px">ABOUT US</a>
    <a class="active" style="left:426px">WHAT WE DO ▾</a>
    <a style="left:505px">REFERRALS</a>
    <a style="left:565px">FEEDBACK</a>
    <a style="left:622px">CONTACT US</a>
  </nav>
</header>

<section class="hero">
  <div class="hero-photo" role="img" aria-label="Carer pushing a young person in a wheelchair on a mountain lookout"></div>
  <div class="hero-tint" role="img" aria-label="Faint pink tree and birds decoration"></div>
  <h1 class="hero-title">VACANCIES</h1>
</section>

<main>
  <article class="card l featured" style="left:91px;top:289px">
    <div class="card-photo" role="img" aria-label="Penrith brick house with garage" style="background:linear-gradient(180deg,#d7dbe0 0%,#8c8478 55%,#5f7a45 100%)"></div>
    <div class="card-head"><h2 class="card-title">PENRITH</h2></div>
    <div class="card-info"><div class="bed"><svg width="17" height="10" viewBox="0 0 17 10"><rect x="0" y="0" width="2" height="10" fill="#3fd0c2"/><rect x="3" y="2" width="4" height="3" rx="1.5" fill="#3fd0c2"/><rect x="7" y="2" width="10" height="4" rx="1" fill="#3fd0c2"/><rect x="0" y="6" width="17" height="2" fill="#3fd0c2"/><rect x="15" y="6" width="2" height="4" fill="#3fd0c2"/></svg>4 Bedroom</div><div>SIL Home</div></div>
    <div class="card-grass"></div>
  </article>

  <article class="card r" style="left:386px;top:289px">
    <div class="card-photo" role="img" aria-label="Mount Druitt red brick house with paved driveway" style="background:linear-gradient(180deg,#7fb2e0 0%,#a0524a 40%,#b57c66 100%)"></div>
    <div class="card-head"><h2 class="card-title">MOUNT<br>DRUITT</h2></div>
    <div class="card-info"><div class="bed"><svg width="17" height="10" viewBox="0 0 17 10"><rect x="0" y="0" width="2" height="10" fill="#3fd0c2"/><rect x="3" y="2" width="4" height="3" rx="1.5" fill="#3fd0c2"/><rect x="7" y="2" width="10" height="4" rx="1" fill="#3fd0c2"/><rect x="0" y="6" width="17" height="2" fill="#3fd0c2"/><rect x="15" y="6" width="2" height="4" fill="#3fd0c2"/></svg>4 Bedroom</div><div>SIL Home</div></div>
    <div class="card-grass"></div>
  </article>

  <article class="card l" style="left:91px;top:454px">
    <div class="card-photo" role="img" aria-label="Casula cream rendered house" style="background:linear-gradient(180deg,#4ea0e6 0%,#e6d9a8 50%,#7a9a55 100%)"></div>
    <div class="card-head"><h2 class="card-title">CASULA</h2></div>
    <div class="card-info"><div class="bed"><svg width="17" height="10" viewBox="0 0 17 10"><rect x="0" y="0" width="2" height="10" fill="#3fd0c2"/><rect x="3" y="2" width="4" height="3" rx="1.5" fill="#3fd0c2"/><rect x="7" y="2" width="10" height="4" rx="1" fill="#3fd0c2"/><rect x="0" y="6" width="17" height="2" fill="#3fd0c2"/><rect x="15" y="6" width="2" height="4" fill="#3fd0c2"/></svg>4 Bedroom</div><div>SIL Home</div></div>
    <div class="card-grass"></div>
  </article>

  <article class="card r" style="left:386px;top:454px">
    <div class="card-photo" role="img" aria-label="Eastwood heritage house with front steps" style="background:linear-gradient(180deg,#6aaee8 0%,#d8c7a8 45%,#6f9a4a 100%)"></div>
    <div class="card-head"><h2 class="card-title">EASTWOOD</h2></div>
    <div class="card-info"><div class="bed"><svg width="17" height="10" viewBox="0 0 17 10"><rect x="0" y="0" width="2" height="10" fill="#3fd0c2"/><rect x="3" y="2" width="4" height="3" rx="1.5" fill="#3fd0c2"/><rect x="7" y="2" width="10" height="4" rx="1" fill="#3fd0c2"/><rect x="0" y="6" width="17" height="2" fill="#3fd0c2"/><rect x="15" y="6" width="2" height="4" fill="#3fd0c2"/></svg>4 Bedroom</div><div>SIL Home</div></div>
    <div class="card-grass"></div>
  </article>

  <article class="card l" style="left:91px;top:619px">
    <div class="card-photo" role="img" aria-label="Baulkham Hills house with palm tree and lawn" style="background:linear-gradient(180deg,#5eaae8 0%,#c9b59a 50%,#4f9a3c 100%)"></div>
    <div class="card-head"><h2 class="card-title">BAULKHAM<br>HILLS</h2></div>
    <div class="card-info"><div class="bed"><svg width="17" height="10" viewBox="0 0 17 10"><rect x="0" y="0" width="2" height="10" fill="#3fd0c2"/><rect x="3" y="2" width="4" height="3" rx="1.5" fill="#3fd0c2"/><rect x="7" y="2" width="10" height="4" rx="1" fill="#3fd0c2"/><rect x="0" y="6" width="17" height="2" fill="#3fd0c2"/><rect x="15" y="6" width="2" height="4" fill="#3fd0c2"/></svg>4 Bedroom</div><div>SIL Home</div></div>
    <div class="card-grass"></div>
  </article>

  <article class="card r" style="left:386px;top:619px">
    <div class="card-photo" role="img" aria-label="Merrylands brick house with long driveway" style="background:linear-gradient(180deg,#6ea8de 0%,#b0664a 40%,#6fa54a 70%,#d0d0c8 100%)"></div>
    <div class="card-head"><h2 class="card-title">MERRYLANDS</h2></div>
    <div class="card-info"><div class="bed"><svg width="17" height="10" viewBox="0 0 17 10"><rect x="0" y="0" width="2" height="10" fill="#3fd0c2"/><rect x="3" y="2" width="4" height="3" rx="1.5" fill="#3fd0c2"/><rect x="7" y="2" width="10" height="4" rx="1" fill="#3fd0c2"/><rect x="0" y="6" width="17" height="2" fill="#3fd0c2"/><rect x="15" y="6" width="2" height="4" fill="#3fd0c2"/></svg>4 Bedroom</div><div>SIL Home</div></div>
    <div class="card-grass"></div>
  </article>

  <article class="card l" style="left:91px;top:784px">
    <div class="card-photo" role="img" aria-label="Harris Park timber building with stairs" style="background:linear-gradient(180deg,#3a6fb0 0%,#2c2a2a 40%,#7a5a45 100%)"></div>
    <div class="card-head"><h2 class="card-title">HARRIS<br>PARK</h2></div>
    <div class="card-info"><div class="bed"><svg width="17" height="10" viewBox="0 0 17 10"><rect x="0" y="0" width="2" height="10" fill="#3fd0c2"/><rect x="3" y="2" width="4" height="3" rx="1.5" fill="#3fd0c2"/><rect x="7" y="2" width="10" height="4" rx="1" fill="#3fd0c2"/><rect x="0" y="6" width="17" height="2" fill="#3fd0c2"/><rect x="15" y="6" width="2" height="4" fill="#3fd0c2"/></svg>4 Bedroom</div><div>SIL Home</div></div>
    <div class="card-grass"></div>
  </article>

  <article class="card r" style="left:386px;top:784px">
    <div class="card-photo" role="img" aria-label="Parramatta two-storey colonial house on lawn" style="background:linear-gradient(180deg,#5a9ee0 0%,#d8d0b8 45%,#7aa84a 75%,#6a9a3a 100%)"></div>
    <div class="card-head"><h2 class="card-title">PARRAMATTA</h2></div>
    <div class="card-info"><div class="bed"><svg width="17" height="10" viewBox="0 0 17 10"><rect x="0" y="0" width="2" height="10" fill="#3fd0c2"/><rect x="3" y="2" width="4" height="3" rx="1.5" fill="#3fd0c2"/><rect x="7" y="2" width="10" height="4" rx="1" fill="#3fd0c2"/><rect x="0" y="6" width="17" height="2" fill="#3fd0c2"/><rect x="15" y="6" width="2" height="4" fill="#3fd0c2"/></svg>4 Bedroom</div><div>SIL Home</div></div>
    <div class="card-grass"></div>
  </article>
</main>

<footer class="footer">
  <div class="foot-brand"><span class="brand-dot"></span>Tallowcrest Care</div>

  <div class="contact" style="top:123px"><svg viewBox="0 0 8 8"><rect x=".5" y="1.5" width="7" height="5" fill="none" stroke="#f64aa0"/><path d="M.5 1.5 4 4.5 7.5 1.5" fill="none" stroke="#f64aa0"/></svg>Email: info@tallowcrestcare.com.au</div>
  <div class="contact" style="top:136px"><svg viewBox="0 0 8 8"><path d="M1 1.2 2.6.6 3.6 2.6 2.7 3.4C3.2 4.4 3.8 5 4.8 5.4L5.6 4.5 7.4 5.5 6.9 7.1C3.6 7 1 4.4 1 1.2Z" fill="#f64aa0"/></svg>Phone: +61 0400 118 532</div>
  <div class="contact" style="top:149px"><svg viewBox="0 0 8 8"><circle cx="4" cy="4" r="3.4" fill="none" stroke="#f64aa0"/><path d="M4 2v2.2l1.4.9" fill="none" stroke="#f64aa0"/></svg>Operating Hours: 9AM To 5PM Monday - Friday</div>

  <div class="social badge" style="top:34px"></div>
  <div class="social" style="top:58px"></div>
  <div class="social" style="top:82px;background:#1e2a4f"></div>
  <div class="social" style="top:107px"></div>

  <div class="foot-col" style="left:385px">
    <h3>ACCOMMODATION</h3>
    <ul>
      <li>Supported Independent Living (SIL)</li>
      <li>Specialist Disability<br>Accommodation (SDA)</li>
      <li>Short term Accommodation<br>(Respite)</li>
      <li>Vacancies</li>
    </ul>
  </div>
  <div class="foot-col" style="left:538px">
    <h3>WHAT WE DO</h3>
    <ul>
      <li>In Home Care</li>
      <li>Social &amp; Community Services</li>
      <li>Therapeutic Supports</li>
      <li>Support Coordination</li>
      <li>Home Modifications</li>
    </ul>
  </div>
</footer>

<div class="bottom-bar">© Copyright 2024 | Tallowcrest Care | All Rights Reserved.
  <div class="to-top"><svg width="7" height="5" viewBox="0 0 7 5"><path d="M0 5 3.5 0 7 5Z" fill="#fff"/></svg></div>
</div>

</body>
</html>
```